Venture Capital Firm Needs Website Redesign

We need a bold revamp of our website (https://halverine.vc/)
which at the moment looks washed out. We want a crisp, fresh and unique look. Feel free to keep as much or as little content in the site. The only thing we need to keep is a team section. The site should convey a clear distinction between our 3 product lines: Venture Capital, Private Credit, and Crypto. Two versions of our logo are attached and they should not change. For design inspirations, we like http://www.9plm.com/ for a more simple site and for a more built out site we like http://bluetorch.com/

Updates
Industry/Entity Type
Investment
Coding
Coded - Design and coding required
Number of Pages Required
1 page
Font styles to use
Colors
Designer to choose colors to be used in the design.
Requirements
Must have
- - Clear distinction between our 3 product lines: Venture Capital, Private Credit
- - Team section

Nice to have
- Some really creative aspect like http://www.9plm.com/ has with the distinction between first, second, and third kind

```html
<!DOCTYPE html>
<html lang="en">
<head>
<meta charset="utf-8">
<title>Halverine</title>
<link rel="stylesheet" href="https://fonts.googleapis.com/css2?family=Open+Sans:wght@400;600;700&family=Questrial&display=swap">
<style>
:root{
  --indigo:#363a86;
  --blue-deep:#1036a6;
  --blue-soft:#8ea4e6;
  --lime:#b6c424;
  --olive:#8d9f3c;
  --ink:#222;
  --muted:#8a8a8a;
  --faint:#dcdcdc;
  --white:#fff;
  --footer-dark:#383838;
}
*{margin:0;padding:0;box-sizing:border-box}
html,body{width:1200px;height:2514px;overflow:hidden}
body{position:relative;background:var(--white);font-family:"Open Sans",Arial,sans-serif;color:var(--ink)}
.abs{position:absolute}
.wordmark{font-family:"Questrial",Arial,sans-serif;letter-spacing:1px}

/* hero */
.hero{left:0;top:0;width:1200px;height:558px;overflow:hidden;background:linear-gradient(115deg,#1238a8 0%,#2f5a9c 38%,#6f9560 68%,#98b046 100%)}
.hero-shapes{position:absolute;left:0;top:0}
.brand{left:161px;top:32px;font-size:38px;color:var(--white)}
.nav{left:555px;top:48px;display:flex;width:484px;justify-content:space-between}
.nav a{color:rgba(255,255,255,.8);font-size:10.5px;font-weight:600;text-decoration:none;letter-spacing:.6px}
.nav a.active{color:var(--white);font-weight:700}
.hero h1{left:150px;top:232px;width:900px;text-align:center;color:var(--white);font-size:34px;font-weight:700;line-height:47px}

/* venture */
.venture{left:0;top:558px;width:1200px;height:612px;background:var(--indigo)}
.section-title{font-size:26px;font-weight:400;font-family:"Questrial",Arial,sans-serif;letter-spacing:.5px}
.ghost{font-size:36px;font-family:"Questrial",Arial,sans-serif;letter-spacing:1px}
.venture .section-title{left:161px;top:62px;color:var(--white)}
.venture .ghost{left:161px;top:104px;color:rgba(255,255,255,.18)}
.venture p{left:600px;top:62px;width:440px;font-size:10.5px;line-height:20px;color:rgba(255,255,255,.55)}
.venture .rule{left:0;top:226px;width:1200px;height:1px;background:rgba(255,255,255,.12)}
.portfolio{left:277px;top:288px;display:flex;gap:42px}
.portfolio .card{width:145px;height:148px;background:linear-gradient(180deg,rgba(255,255,255,.07),rgba(255,255,255,0));display:flex;justify-content:center;padding-top:38px;color:var(--white);font-size:26px;font-family:"Questrial",Arial,sans-serif}
.portfolio .card.small{font-size:17px;padding-top:46px}

.curve{left:0;top:990px}
.credit .section-title{left:161px;top:1093px;color:var(--indigo);font-weight:700;font-family:"Open Sans",Arial,sans-serif;font-size:24px}
.credit .ghost{left:161px;top:1136px;color:#e4e4d8}
.credit p{left:481px;top:1094px;width:560px;font-size:11px;line-height:20px;color:#666}
.credit .rule{left:161px;top:1245px;width:878px;height:1px;background:var(--faint)}
.partner{top:1297px;width:138px;height:138px}
.partner span{position:absolute;left:20px;top:20px;width:98px;height:98px;display:flex;align-items:center;justify-content:center;text-align:center;font-family:"Questrial",Arial,sans-serif;font-size:16px;line-height:19px;color:var(--indigo)}

/* crypto */
.crypto{left:161px;top:1500px;width:1039px;height:416px;border-radius:16px 0 0 16px;background:linear-gradient(90deg,var(--blue-soft) 0%,#5f7ad8 40%,var(--blue-deep) 100%)}
.crypto .section-title{left:44px;top:56px;color:var(--white);font-weight:700;font-family:"Open Sans",Arial,sans-serif;font-size:24px}
.crypto .ghost{left:44px;top:100px;color:rgba(190,200,60,.55)}
.crypto p{left:44px;top:172px;width:380px;font-size:11px;line-height:20px;color:var(--white)}
.btn{left:44px;top:317px;width:96px;height:36px;border:1.5px solid var(--white);color:var(--white);font-size:10px;font-weight:600;display:flex;align-items:center;justify-content:center}
.chart{left:620px;top:1450px}

/* team */
.member{top:2013px;width:300px;text-align:center}
.member .photo{position:relative;width:246px;height:246px;margin:0 auto}
.member .portrait{position:absolute;left:10px;top:10px;width:226px;height:226px;border-radius:50%;background:radial-gradient(circle at 50% 40%,#e3e3e3 0%,#9a9a9a 60%,#4a4a4a 100%)}
.member .ring{position:absolute;left:0;top:0}
.member h3{margin-top:12px;font-size:14px;font-weight:700}
.member p{margin:10px auto 0;width:250px;font-size:10.5px;line-height:19px;color:#777}

/* footer */
.footer{left:0;top:2400px;width:1200px;height:81px;background:var(--olive)}
.contact{left:161px;top:31px;display:flex;align-items:center;gap:8px;color:var(--white);font-size:11px}
.contact .gap{width:18px}
.footer-nav{left:670px;top:31px;display:flex;gap:28px}
.footer-nav a{color:var(--white);font-size:11px;font-weight:700;text-decoration:none}
.copyright{left:0;top:2481px;width:1200px;height:33px;background:var(--footer-dark);color:#ddd;font-size:10px;display:flex;align-items:center;justify-content:center}
</style>
</head>
<body>

<header class="abs hero">
  <svg class="hero-shapes" width="1200" height="558" viewBox="0 0 1200 558">
    <circle cx="318" cy="293" r="142" fill="#d79bc0" fill-opacity=".28"/>
    <circle cx="536" cy="100" r="134" fill="#d79bc0" fill-opacity=".22"/>
    <circle cx="213" cy="522" r="84" fill="#e0a8a0" fill-opacity=".35"/>
    <circle cx="486" cy="540" r="84" fill="#e0a8a0" fill-opacity=".35"/>
    <circle cx="1089" cy="640" r="252" fill="#b8c46a" fill-opacity=".35"/>
  </svg>
  <div class="abs brand wordmark">HALVERINE</div>
  <nav class="abs nav">
    <a class="active" href="#">VENTURE</a><a href="#">PRIVATE CREDIT</a><a href="#">CRYPTO</a><a href="#">ABOUT US</a><a href="#">TEAM</a><a href="#">BLOG</a>
  </nav>
  <h1 class="abs">Halverine operates at the intersection of technol-<br>ogy and novel asset classes.</h1>
</header>

<section class="abs venture">
  <h2 class="abs section-title">VENTURE CAPITAL</h2>
  <div class="abs ghost">HALVERINE</div>
  <p class="abs">We invest in early-stage startups led by founders who are passionate and knowledge-able about the markets they serve. We have our own software developers and product managers. We work with the founders in our portfolio to help them bring products to market, earning equity for this work and for the cash we invest in their companies.</p>
  <div class="abs rule"></div>
  <div class="abs portfolio">
    <div class="card">Lumora</div>
    <div class="card">Tinytrip</div>
    <div class="card">Boardlane</div>
    <div class="card small">Northway Group</div>
  </div>
</section>

<svg class="abs curve" width="1200" height="700" viewBox="0 990 1200 700">
  <path d="M0 1168 C 180 1040 420 994 720 994 L1200 994 L1200 1690 L0 1690 Z" fill="#fff"/>
  <path d="M0 1230 C 60 1200 110 1190 160 1190 L160 1690 L0 1690 Z" fill="#f6f6f6"/>
</svg>

<section class="credit">
  <h2 class="abs section-title">PRIVATE CREDIT</h2>
  <div class="abs ghost">HALVERINE</div>
  <p class="abs">Halverine Private Credit provides capital to lending businesses that are focused on using technology to establish new credit markets, create new credit products or dramatically re-invent an existing form of credit. We believe that the pioneers who build something truly different in a credit market will create the most sus-tainable business models. Given our heritage as a venture firm, we are comfortable with emerging businesses and can provide capital for a company's first loan.</p>
  <div class="abs rule"></div>
  <div class="abs partner" style="left:167px">
    <svg width="138" height="138" viewBox="0 0 138 138"><circle cx="69" cy="69" r="64" fill="none" stroke="#1b1b1b" stroke-width="3"/><circle cx="5" cy="69" r="6" fill="#3a3a3a"/><circle cx="133" cy="69" r="6" fill="#3a3a3a"/></svg>
    <span>Verdant</span>
  </div>
  <div class="abs partner" style="left:342px">
    <svg width="138" height="138" viewBox="0 0 138 138"><circle cx="69" cy="69" r="64" fill="none" stroke="#1b1b1b" stroke-width="3"/><circle cx="5" cy="69" r="6" fill="#3a3a3a"/><circle cx="133" cy="69" r="6" fill="#3a3a3a"/></svg>
    <span>Pellmark<br>Finance</span>
  </div>
  <div class="abs partner" style="left:518px">
    <svg width="138" height="138" viewBox="0 0 138 138"><circle cx="69" cy="69" r="64" fill="none" stroke="#1b1b1b" stroke-width="3"/><circle cx="5" cy="69" r="6" fill="#3a3a3a"/><circle cx="133" cy="69" r="6" fill="#3a3a3a"/></svg>
    <span>Brightledger</span>
  </div>
</section>

<section class="abs crypto">
  <h2 class="abs section-title">CRYPTO</h2>
  <div class="abs ghost">HALVERINE</div>
  <p class="abs">The Halverine Crypto Index tracks the top 15 cryptocurrencies weighted by market cap and rebalanced twice a month. We believe this is the simplest and most cost effective way to obtain cryptocur-rency exposure. Our process has been designed by experts from finan-cial services and cryptocurrency industries.</p>
  <div class="abs btn">Learn More</div>
</section>

<svg class="abs chart" width="436" height="419" viewBox="0 0 260 250" font-family="Open Sans, Arial, sans-serif">
  <text x="113" y="67" font-size="4.5" font-weight="700" fill="#fff" text-anchor="middle">HXI™ Cumulative Growth</text>
  <circle cx="76" cy="80" r="3.5" fill="#c6cc1e"/><text x="82" y="82" font-size="4.5" fill="#fff">HXI™ (1236.48%)</text>
  <circle cx="136" cy="80" r="3.5" fill="#111"/><text x="142" y="82" font-size="4.5" fill="#fff">Bitcoin (717.41%)</text>
  <g font-size="4" fill="#fff" text-anchor="end">
    <text x="28" y="238">0</text><text x="28" y="216.5">500</text><text x="28" y="195">1000</text><text x="28" y="173.4">1500</text>
    <text x="28" y="151.8">2000</text><text x="28" y="130.3">2500</text><text x="28" y="108.7">3000</text><text x="28" y="87.2">3500</text>
  </g>
  <g font-size="4" fill="#fff" text-anchor="middle">
    <text x="31" y="246">Jan</text><text x="45" y="246">Feb</text><text x="60" y="246">Mar</text><text x="74" y="246">Apr</text><text x="89" y="246">May</text><text x="104" y="246">Jun</text><text x="118" y="246">Jul</text><text x="133" y="246">Aug</text><text x="148" y="246">Sep</text><text x="162" y="246">Oct</text><text x="177" y="246">Nov</text><text x="192" y="246">Dec</text><text x="206" y="246">Jan</text><text x="221" y="246">Feb</text><text x="235" y="246">Mar</text>
  </g>
  <polyline fill="none" stroke="#c6cc1e" stroke-width="1.1" points="31,237 39,237 47,236.6 55,235.7 62,235.3 70,234.4 78,233.6 86,230.5 94,226.2 102,217.6 110,218.5 117,226.2 125,213.3 133,209 141,215.5 149,204.7 157,202.5 164,198.2 172,176.7 180,133.6 188,125 196,103.4 204,137.9 212,150.8 219,148.6 227,168 235,183.1"/>
  <g fill="#c6cc1e"><circle cx="102" cy="217.6" r="1.2"/><circle cx="125" cy="213.3" r="1.2"/><circle cx="149" cy="204.7" r="1.2"/><circle cx="172" cy="176.7" r="1.2"/><circle cx="196" cy="103.4" r="1.2"/><circle cx="212" cy="150.8" r="1.2"/><circle cx="235" cy="183.1" r="1.2"/></g>
  <polyline fill="none" stroke="#111" stroke-width="1.1" points="31,237 39,237 47,236.8 55,236.6 62,236.1 70,235.7 78,235.3 86,233.6 94,230.5 102,226.2 110,226.7 117,230.5 125,224.1 133,221.9 141,224.1 149,218.9 157,217.6 164,215.5 172,202.5 180,185.3 188,163.7 196,176.7 204,174.5 212,189.6 219,196.1 227,191.7 235,206.8"/>
</svg>

<section class="team">
  <div class="abs member" style="left:135px">
    <div class="photo">
      <div class="portrait" role="img" aria-label="Black and white portrait of Daniel Reyes"></div>
      <svg class="ring" width="246" height="246" viewBox="0 0 246 246"><circle cx="123" cy="123" r="117" fill="none" stroke="#1b1b1b" stroke-width="4"/><circle cx="6" cy="123" r="9" fill="#3a3a3a"/><circle cx="240" cy="123" r="9" fill="#3a3a3a"/></svg>
    </div>
    <h3>Daniel Reyes</h3>
    <p>Daniel is a Partner for Halverine VC Fund. He is also a cofounder of Halverine.</p>
  </div>
  <div class="abs member" style="left:450px">
    <div class="photo">
      <div class="portrait" role="img" aria-label="Black and white portrait of Marco Lindqvist"></div>
      <svg class="ring" width="246" height="246" viewBox="0 0 246 246"><circle cx="123" cy="123" r="117" fill="none" stroke="#1b1b1b" stroke-width="4"/><circle cx="6" cy="123" r="9" fill="#3a3a3a"/><circle cx="240" cy="123" r="9" fill="#3a3a3a"/></svg>
    </div>
    <h3>Marco Lindqvist</h3>
    <p>Marco is a Partner for Halverine Crypto. He previ-ously invested at Harbor Capital and Keel</p>
  </div>
  <div class="abs member" style="left:765px">
    <div class="photo">
      <div class="portrait" role="img" aria-label="Black and white portrait of Samir Oduya"></div>
      <svg class="ring" width="246" height="246" viewBox="0 0 246 246"><circle cx="123" cy="123" r="117" fill="none" stroke="#1b1b1b" stroke-width="4"/><circle cx="6" cy="123" r="9" fill="#3a3a3a"/><circle cx="240" cy="123" r="9" fill="#3a3a3a"/></svg>
    </div>
    <h3>Samir Oduya</h3>
    <p>Samir is a Partner for Halverine VC Fund. He is also a cofounder of Halverine and Gridcraft</p>
  </div>
</section>

<footer class="abs footer">
  <div class="abs contact">
    <svg width="12" height="16" viewBox="0 0 12 16"><path d="M6 0a6 6 0 0 0-6 6c0 4.5 6 10 6 10s6-5.5 6-10a6 6 0 0 0-6-6z" fill="#fff"/><circle cx="6" cy="6" r="2.2" fill="#8d9f3c"/></svg>
    <span>218 Alder Street, Suite 400, Portland, OR, 97204</span>
    <span class="gap"></span>
    <svg width="15" height="10" viewBox="0 0 15 10"><rect width="15" height="10" rx="1" fill="#fff"/><path d="M0.5 0.8 7.5 5.5 14.5 0.8" fill="none" stroke="#8d9f3c" stroke-width="1.2"/></svg>
    <span>hello@halverine.vc</span>
  </div>
  <nav class="abs footer-nav">
    <a href="#">Venture</a><a href="#">Private Credit</a><a href="#">Crypto</a><a href="#">About Us</a><a href="#">Team</a><a href="#">Blog</a>
  </nav>
</footer>
<div class="abs copyright">Copyright © 2018 Halverine All Rights Reserved.</div>

</body>
</html>
```